Jolly Paws Business Card Update

I have a business card which I love. I want to keep the same logo, colours, font and style. I want to upgrade the scripting and remove some elements and add others.
On the front side under Services - remove the existing wording and insert - Providing individual coaching strategies to create happy, healthy and social canine companions
Under Denise Carvell amend the current wording to read: Qualified in Dog Behavioural Training, Natural Animal Healthcare and Animal Health Science
On the reverse side to remove the web address.

```html
<!DOCTYPE html>
<html lang="en">
<head>
<meta charset="utf-8">
<title>Jolly Paws Business Card</title>
<link href="https://fonts.googleapis.com/css2?family=Arimo:wght@400;700&family=Ubuntu:wght@400;500&display=swap" rel="stylesheet">
<style>
  :root {
    --bg: #2a2a2a;
    --blue-light: #0897d2;
    --blue-mid: #1670bd;
    --blue-deep: #2c3580;
    --navy-text: #27307f;
    --red: #c8202a;
    --red-dark: #8c1a1f;
    --paper: #f1f1f1;
    --cream: #efe8d2;
    --white-soft: #e9ebf5;
  }
  * { margin: 0; padding: 0; box-sizing: border-box; }
  html, body { width: 1200px; height: 1138px; overflow: hidden; background: var(--bg); }
  .canvas { position: relative; width: 1200px; height: 1138px; }

  .card { position: absolute; border-radius: 14px; overflow: hidden; }

  /* Front */
  .card-front {
    left: 274px; top: 186px; width: 623px; height: 376px;
    background: linear-gradient(180deg, var(--blue-light) 0%, var(--blue-mid) 45%, var(--blue-deep) 100%);
  }
  .front-emblem {
    position: absolute; left: 235px; top: 74px; width: 150px; height: 150px;
    border-radius: 50%; background: var(--cream); border: 10px solid var(--red-dark);
  }
  .front-name {
    position: absolute; left: 0; right: 0; top: 226px; text-align: center;
    font-family: "Arimo", sans-serif; font-weight: 700; font-size: 40px;
    color: var(--white-soft); letter-spacing: 1px;
  }
  .front-tagline {
    position: absolute; left: 0; right: 0; top: 276px; text-align: center;
    font-family: "Arimo", sans-serif; font-size: 18.5px; color: var(--white-soft);
  }

  /* Back */
  .card-back {
    left: 276px; top: 608px; width: 619px; height: 374px; background: var(--paper);
  }
  .back-shapes { position: absolute; inset: 0; }
  .back-emblem {
    position: absolute; left: 50px; top: 96px; width: 168px; height: 168px;
    border-radius: 50%; background: var(--cream); border: 12px solid var(--red-dark);
  }
  .back-name {
    position: absolute; left: 0; width: 268px; top: 282px; text-align: center;
    font-family: "Arimo", sans-serif; font-weight: 700; font-size: 20px; color: var(--white-soft);
  }
  .contact {
    position: absolute; right: 29px; top: 34px; text-align: right;
    font-family: "Ubuntu", sans-serif; color: var(--navy-text);
  }
  .person-name { font-weight: 500; font-size: 26px; line-height: 1.2; }
  .qualifications { font-size: 14px; line-height: 20px; margin-top: 6px; }
  .contact-list { list-style: none; margin-top: 8px; font-size: 15px; line-height: 22px; }
  .contact-list li { display: flex; justify-content: flex-end; align-items: center; gap: 8px; }
  .contact-list svg { width: 12px; height: 12px; fill: var(--red); }

  .services {
    position: absolute; right: 29px; top: 228px; text-align: right;
    font-family: "Arimo", sans-serif; color: #fff; font-size: 16px; line-height: 19px;
  }
  .services h2 { font-size: 16px; font-weight: 700; }
  .mission {
    position: absolute; right: 29px; top: 320px; text-align: right;
    font-family: "Arimo", sans-serif; color: var(--navy-text); font-size: 16px; line-height: 19px;
  }
</style>
</head>
<body>
<div class="canvas">

  <section class="card card-front">
    <div class="front-emblem" role="img" aria-label="Brand emblem area"></div>
    <div class="front-name">JOLLY PAWS</div>
    <div class="front-tagline">HAPPY DOGS, HAPPY OWNERS</div>
  </section>

  <section class="card card-back">
    <svg class="back-shapes" viewBox="0 0 619 374" width="619" height="374" aria-hidden="true">
      <defs>
        <linearGradient id="sideBlue" x1="0" y1="0" x2="0" y2="1">
          <stop offset="0" stop-color="#1562b4"/>
          <stop offset="0.5" stop-color="#1479bf"/>
          <stop offset="1" stop-color="#1a6cc0"/>
        </linearGradient>
        <linearGradient id="bandRed" x1="0" y1="0" x2="1" y2="0">
          <stop offset="0" stop-color="#7d171c"/>
          <stop offset="0.45" stop-color="#cc1f27"/>
          <stop offset="1" stop-color="#8c1a1f"/>
        </linearGradient>
      </defs>
      <path d="M0 0 H236 Q330 160 268 310 L270 216 H619 V310 H255 Z" fill="url(#bandRed)"/>
      <rect x="240" y="216" width="379" height="94" fill="url(#bandRed)"/>
      <path d="M0 0 H210 Q315 190 216 374 H0 Z" fill="url(#sideBlue)"/>
    </svg>

    <div class="back-emblem" role="img" aria-label="Brand emblem area"></div>
    <div class="back-name">JOLLY PAWS</div>

    <div class="contact">
      <h1 class="person-name">Denise Carvell</h1>
      <p class="qualifications">Qualified in Dog Behavioural<br>Training, Natural Animal Healthcare<br>and Animal Health Science</p>
      <ul class="contact-list">
        <li>0400 123 456
          <svg viewBox="0 0 12 12"><path d="M3 0h6a1 1 0 0 1 1 1v10a1 1 0 0 1-1 1H3a1 1 0 0 1-1-1V1a1 1 0 0 1 1-1zm0 2v5h6V2z"/></svg></li>
        <li>jollypaws1@mail.com
          <svg viewBox="0 0 12 12"><path d="M0 2h12v1.2L6 7 0 3.2zM0 4.6 6 8.4l6-3.8V10H0z"/></svg></li>
        <li>www.jollypaws1.com
          <svg viewBox="0 0 12 12"><circle cx="6" cy="6" r="5.5"/><path d="M0.5 6h11M6 0.5v11" stroke="#f1f1f1" stroke-width="0.8"/></svg></li>
      </ul>
    </div>

    <div class="services">
      <h2>SERVICES</h2>
      <p>Providing individual coaching<br>strategies to create happy, healthy<br>and social canine companions</p>
    </div>

    <p class="mission">Promoting communication and connection<br>between dogs &amp; their families</p>
  </section>

</div>
</body>
</html>
```